Corvane Freight Company Business Card Design

We are a company that delivers natural saltwater (from the ocean) to aquarium companies, restaurants and home marine tanks. I would like a new business card to suit.

Must include Name, company name, abn, contact number and website as well as logo (see attached).

Looking for a design that stands out, has a clean but unique appearance.

Double and single sided entries welcome

Business

• Logo

```html
<!DOCTYPE html>
<html lang="en">
<head>
<meta charset="utf-8">
<title>Corvane Freight Company Business Card</title>
<link href="https://fonts.googleapis.com/css2?family=Source+Sans+3:wght@400;600;700&display=swap" rel="stylesheet">
<style>
  :root {
    --backdrop: #141414;
    --card-white: #ffffff;
    --brand-blue: #0795d2;
    --logo-blue: #2a9ad6;
    --deep-blue: #1a5fb0;
    --ink: #1e1e1e;
  }
  * { margin: 0; padding: 0; box-sizing: border-box; }
  html, body {
    width: 1200px; height: 420px; overflow: hidden;
    background: var(--backdrop);
    font-family: "Source Sans 3", Arial, sans-serif;
  }
  .stage { position: relative; width: 1200px; height: 420px; }
  .card {
    position: absolute; top: 65px; width: 525px; height: 300px;
    border-radius: 22px; overflow: hidden;
  }
  .card-front { left: 70px; background: var(--card-white); }
  .card-back { left: 632px; background: var(--brand-blue); }

  .front-wave { position: absolute; left: 0; bottom: 0; width: 525px; height: 300px; }

  .wordmark {
    position: absolute; left: 24px; top: 118px;
    font-size: 38px; font-weight: 400; color: var(--logo-blue);
    letter-spacing: -0.5px; white-space: nowrap;
  }
  .details {
    position: absolute; left: 342px; top: 72px;
    color: var(--ink); font-size: 13px; line-height: 19px;
  }
  .details .abn { margin-top: 17px; }
  .details .contact-line { display: flex; align-items: center; gap: 8px; }
  .details .phone { margin-top: 13px; }
  .details svg { width: 10px; height: 10px; flex: none; }

  .signature {
    position: absolute; right: 38px; bottom: 19px;
    color: var(--card-white); font-size: 17px;
  }
  .signature strong { font-weight: 700; }
  .signature span { font-size: 15px; font-weight: 400; }

  .back-wordmark {
    position: absolute; left: 0; right: 0; top: 120px; text-align: center;
    font-size: 58px; font-weight: 400; color: var(--card-white);
    letter-spacing: -1px; white-space: nowrap;
  }
</style>
</head>
<body>
<main class="stage">
  <section class="card card-front" aria-label="Business card front">
    <svg class="front-wave" viewBox="0 0 525 300" aria-hidden="true">
      <path d="M0 262 C 130 250, 300 215, 525 238 L525 300 L0 300 Z" fill="var(--brand-blue)"/>
      <path d="M150 262 C 290 238, 420 218, 525 232" fill="none" stroke="var(--deep-blue)" stroke-width="4"/>
      <path d="M120 266 C 280 240, 420 226, 525 240" fill="none" stroke="var(--card-white)" stroke-width="2"/>
    </svg>

    <div class="wordmark">Corvane Freight</div>

    <div class="details">
      <p>Street Name, City Name ,<br>State, Zip Code</p>
      <p class="abn">ABN: 123456789</p>
      <p class="contact-line phone">
        <svg viewBox="0 0 10 10" aria-hidden="true"><circle cx="5" cy="5" r="4.5" fill="none" stroke="var(--ink)"/><path d="M3.2 2.6 L4.3 3.7 L3.8 4.3 Q4.6 5.6 5.7 6.2 L6.3 5.7 L7.4 6.8 L6.6 7.6 Q3.6 6.6 2.4 3.4 Z" fill="var(--ink)"/></svg>
        123-456-7892
      </p>
      <p class="contact-line">
        <svg viewBox="0 0 10 10" aria-hidden="true"><circle cx="5" cy="5" r="4.5" fill="var(--ink)"/><path d="M0.5 5 H9.5 M5 0.5 V9.5 M5 0.5 Q2 5 5 9.5 M5 0.5 Q8 5 5 9.5" fill="none" stroke="var(--card-white)" stroke-width="0.7"/></svg>
        www.corvanefreight.com
      </p>
    </div>

    <p class="signature"><strong>Your Name,</strong> <span>Title</span></p>
  </section>

  <section class="card card-back" aria-label="Business card back">
    <div class="back-wordmark">Corvane Freight</div>
  </section>
</main>
</body>
</html>
```